verdant terraces simple classy business card design

my name is colin barrow and I run a gardening business aimed at high class verdant terraces. the business name is verdant terraces and our logo was designed on pixel harbour .My clientel are anything from residential homes to businesses. I take pride in my work and know that I offer a service like no other in my area.
The business card will be used to represent my business and I want it to be not only rememberable, but simplistic and modern. Eye catching too. Of course I would like it relatable to gardening and appealing to the correct clientel - those being garden enthusiasts, prestigious homes and businesses that are after top of the line gardening services like no other on the market.
I am not a typical lawn mowing business so I don't want a typical card design that represents that. The gardens I work with are generally million dollar properties with owners who are very garden proud looking for upkeep and guidance from me along with sometimes whole new garden designs. I want the business cards to show to my clients that I take pride, as they do, in their garden. And I want them to know from my card that I am a professional, qualified horticulturist offering them a top of the line service for life. I want them to refer my business on. I want them to look at my business card and see class and professionalism in a modern unique bold way.
The card should be simple with the possibility of the logo on the front being embossed/debossed and my details on the back the card should have a organic garden feel it's very important to me that it is absolutely perfect
I am also very open to ideas and suggestions so look forward to seeing the designs. the business logo has been supplied with this project and I want the card to be double sided

Contact info is
Colin Barrow - Managing Director / Horticulturist
Phone : 0481 526 704
Email: colinbarrow@verdantterraces.example.au

Target Market(s)

high class gardens residential and commercial

Industry/Entity Type

Gardener

Contact Information for Business Card

Contact info is
Phone : 0481 526 704

PLEASE MAKE CARD DOUBLE SIDED

Requirements
Must have
• organic simple classy modern feel
• must flow with the current logo that has been supplied with this project
• Double sided
• Must explain in a simple way that I deal with high end gardens and I'm a qualified horticulturist
Nice to have
• embossed debossed logo
Should not have
• shouldn't be to busy or cheap looking

```html
<!DOCTYPE html>
<html lang="en">
<head>
<meta charset="utf-8">
<title>Verdant Terraces – Business Card</title>
<link rel="stylesheet" href="https://fonts.googleapis.com/css2?family=Arimo:wght@400;700&display=swap">
<style>
  :root {
    --backdrop: #8d8d8d;
    --leaf-green: #4f8744;
    --paper: #e9eaed;
    --ink-light: #f2f3f1;
  }
  * { margin: 0; padding: 0; box-sizing: border-box; }
  html, body {
    width: 1105px;
    height: 1200px;
    overflow: hidden;
    background: var(--backdrop);
    font-family: "Arimo", Arial, sans-serif;
  }
  .card {
    position: absolute;
    left: 182px;
    width: 746px;
    height: 426px;
  }
  .card--details { top: 119px; display: flex; }
  .card--brand {
    top: 637px;
    background: var(--leaf-green);
    color: var(--ink-light);
    display: flex;
    flex-direction: column;
    align-items: center;
  }
  .details-panel {
    width: 369px;
    height: 100%;
    background: var(--leaf-green);
    color: var(--ink-light);
    padding: 118px 0 0 29px;
  }
  .person-name { font-size: 24px; font-weight: 700; line-height: 1.2; }
  .person-role { font-size: 19px; line-height: 1.4; margin-top: 6px; }
  .contact-list { list-style: none; margin-top: 22px; font-size: 17px; line-height: 28px; }
  .contact-list .label { font-weight: 700; }
  .contact-list .small { font-size: 16px; }
  .brand-panel {
    flex: 1;
    height: 100%;
    background: var(--paper);
    color: var(--leaf-green);
    display: flex;
    flex-direction: column;
    align-items: center;
    justify-content: center;
    padding-bottom: 10px;
  }
  .brand-mark { display: block; }
  .brand-name {
    font-weight: 700;
    text-transform: uppercase;
    text-align: center;
    letter-spacing: 4px;
    line-height: 1.25;
    margin-top: 14px;
  }
  .brand-panel .brand-name { font-size: 30px; }
  .card--brand .brand-mark { margin-top: 118px; }
  .card--brand .brand-name { font-size: 36px; letter-spacing: 5px; }
  .web-address {
    margin-top: auto;
    margin-bottom: 44px;
    font-size: 19px;
    letter-spacing: 3px;
  }
</style>
</head>
<body>
  <section class="card card--details">
    <div class="details-panel">
      <h1 class="person-name">Colin Barrow</h1>
      <p class="person-role">Managing Director<br>Horticulturist</p>
      <ul class="contact-list">
        <li><span class="label">P :</span> 0481 526 704</li>
        <li class="small">colinbarrow@verdantterraces.example.au</li>
        <li class="small">verdantterraces.example.au</li>
      </ul>
    </div>
    <div class="brand-panel">
      <svg class="brand-mark" width="78" height="78" viewBox="0 0 78 78" aria-hidden="true">
        <circle cx="39" cy="39" r="38" fill="var(--leaf-green)"/>
      </svg>
      <p class="brand-name">Verdant<br>Terraces</p>
    </div>
  </section>

  <section class="card card--brand">
    <svg class="brand-mark" width="104" height="104" viewBox="0 0 104 104" aria-hidden="true">
      <circle cx="52" cy="52" r="51" fill="var(--ink-light)"/>
    </svg>
    <p class="brand-name">Verdant<br>Terraces</p>
    <p class="web-address">www.verdantterraces.example.au</p>
  </section>
</body>
</html>
```